The K7 Momentum Collective Website

We have a pitch deck and messaging drafted. Target audience is academic institutions and VC investors that have seed money in start ups.

Need a basic website

Industry/Entity Type

LIfe Science, Diagnostic, medical device.

Coding

Coded - Design and coding required

Number of Pages Required

5+ page

```html
<!DOCTYPE html>
<html lang="en">
<head>
<meta charset="utf-8">
<title>K7 Momentum Collective</title>
<link href="https://fonts.googleapis.com/css2?family=Lato:wght@400;700;900&display=swap" rel="stylesheet">
<style>
:root{
  --blue:#4472c6;
  --blue-dark:#2f5aa8;
  --ink:#161616;
  --text:#3a3a3a;
  --muted:#f0f2f5;
  --white:#fff;
  --pale-blue:#dfe7f6;
}
*{box-sizing:border-box;margin:0;padding:0}
html,body{width:1200px;height:3366px;overflow:hidden}
body{font-family:'Lato',sans-serif;color:var(--text);background:var(--white);position:relative}
section,header,footer{position:absolute;left:0;width:1200px}
.abs{position:absolute}
.accent{color:var(--blue);font-weight:700}

/* header */
.site-header{top:0;height:104px;background:var(--white)}
.brand{left:110px;top:18px;font-size:30px;font-weight:700;color:var(--ink);white-space:nowrap}
.contact-strip{right:111px;top:23px;display:flex;align-items:center;gap:10px;font-size:15px;font-weight:700;color:var(--blue);white-space:nowrap}
.contact-strip .sep{width:1px;height:20px;background:#bbb;margin:0 6px}
.social{display:flex;gap:8px;margin-left:6px}
.social span{width:28px;height:28px;border:2px solid var(--blue);border-radius:50%}
.main-nav{left:111px;top:71px;width:978px;height:64px;background:var(--blue);border-radius:8px 8px 0 0;display:flex;align-items:center;padding:0 30px;justify-content:space-between;z-index:3}
.main-nav a{color:var(--white);font-size:15px;text-decoration:none}
.main-nav a.current{font-weight:700;text-decoration:underline}
.search-btn{width:26px;height:26px;background:var(--white);border-radius:50%;display:flex;align-items:center;justify-content:center}

/* hero */
.hero{top:104px;height:507px}
.hero-photo{inset:0;background:linear-gradient(180deg,#d9dde0 0%,#c7ccce 40%,#8c8778 70%,#3a3c40 100%)}
.hero h1{left:0;width:1200px;top:72px;text-align:center;font-size:42px;font-weight:900;color:#0d0d0d}
.btn{display:inline-block;background:var(--blue);color:var(--white);font-weight:700;font-size:17px;border-radius:6px;padding:10px 18px;box-shadow:0 3px 6px rgba(0,0,0,.2)}
.hero .btn{left:540px;top:133px}

/* about */
.about{top:611px;height:539px}
.about-accent{left:56px;top:38px;width:150px;height:150px;background:var(--pale-blue)}
.about-photo{left:116px;top:69px;width:416px;height:400px;background:linear-gradient(135deg,#1f3b6b,#3a6bb0 55%,#0f1e38);border:5px solid #fff;box-shadow:0 4px 14px rgba(0,0,0,.2)}
.about h2{left:597px;top:60px;font-size:36px;font-weight:400;color:var(--ink);white-space:nowrap}
.about .copy{left:597px;top:108px;width:500px;font-size:15px;line-height:26px;white-space:nowrap}
.ticks{list-style:none;margin-top:8px}
.ticks li{position:relative;padding-left:23px;margin-bottom:5px}
.ticks svg{position:absolute;left:0;top:8px}
.about .btn{left:598px;top:430px}

/* discovery */
.discovery{top:1150px;height:442px;background:var(--muted)}
.section-title{left:0;width:1200px;text-align:center;font-size:36px;font-weight:400;color:var(--ink)}
.discovery .section-title{top:54px}
.card{top:118px;width:251px;height:263px;background:var(--white);box-shadow:0 2px 10px rgba(0,0,0,.1);text-align:center;padding:24px 6px 0;overflow:hidden}
.card::before{content:"";position:absolute;left:0;top:0;border-top:34px solid var(--blue);border-right:34px solid transparent}
.card h3{font-size:18.5px;font-weight:900;color:var(--ink);margin:14px 0 2px}
.card p{font-size:15px;line-height:26px;white-space:nowrap}
.card.active{background:var(--blue-dark)}
.card.active h3,.card.active p{color:var(--white)}
.card.active::before{display:none}

/* problem */
.problem{top:1592px;height:448px;background:#2c4f8a}
.problem-photo{left:560px;top:0;width:640px;height:448px;background:linear-gradient(110deg,#8fa9cf,#3d5f8f 50%,#1d2f4b)}
.problem-shade{left:0;top:0;width:760px;height:448px;background:linear-gradient(90deg,#4a78c4 0%,#4a78c4 60%,rgba(74,120,196,0) 100%)}
.problem h2{left:111px;top:44px;font-size:36px;font-weight:400;color:var(--white)}
.problem h2 b{font-weight:900}
.problem .copy{left:110px;top:96px;width:500px;color:var(--white);font-size:14.5px;line-height:26px;white-space:nowrap}
.problem .copy li{list-style:none;position:relative;padding-left:21px;margin:4px 0 8px}
.problem .copy li svg{position:absolute;left:0;top:8px}
.btn-light{left:111px;top:339px;background:var(--white);color:var(--blue);font-weight:700;font-size:17px;border-radius:6px;padding:10px 18px}

/* team */
.team{top:2040px;height:573px}
.team .section-title{top:52px}
.member{width:274px;text-align:center}
.member .photo{width:274px;height:260px;background:linear-gradient(180deg,#d6d6d6,#b8b8b8)}
.member .name{display:inline-block;background:var(--white);padding:6px 0 0;width:230px;margin-top:-22px;position:relative;font-size:20px;font-weight:900;color:var(--ink)}
.member.mid .name{color:var(--blue)}
.member p{font-size:15px;line-height:26px;margin-top:4px;white-space:nowrap}
.member .mail{font-size:15px;font-weight:700;color:var(--blue);margin-top:4px;display:flex;gap:10px;justify-content:center;align-items:center}

/* contact */
.contact{top:2613px;height:477px;background:linear-gradient(180deg,#f3f4f6 0%,#f3f4f6 45%,#e6e8ec 100%)}
.contact .section-title{top:40px}
.contact h4{left:113px;top:112px;font-size:21px;font-weight:900;color:var(--ink)}
.info{left:111px;display:flex;align-items:center;gap:12px;font-size:16px;font-weight:700;color:var(--ink);line-height:25px}
.info .ico{width:47px;height:47px;border-radius:50%;background:var(--blue);display:flex;align-items:center;justify-content:center;flex:none}
.field{background:var(--white);font-size:14px;color:#555;padding:0 17px;display:flex;align-items:center}
.contact .btn{left:508px;top:364px;padding:12px 35px}

/* footer */
.site-footer{top:3090px;height:276px;background:var(--blue);color:var(--white);text-align:center}
.site-footer .name{top:74px;left:0;width:1200px;font-size:40px;font-weight:700}
.foot-nav{top:147px;left:0;width:1200px;display:flex;justify-content:center;gap:47px;font-size:15px}
.foot-social{top:193px;left:0;width:1200px;display:flex;justify-content:center;gap:30px}
.foot-social span{width:12px;height:12px;border-radius:50%;background:var(--white)}
.copyright{top:235px;left:0;width:1200px;font-size:15px}
</style>
</head>
<body>

<header class="site-header">
  <div class="abs brand">K7 <span class="accent">Momentum</span> Collective</div>
  <div class="abs contact-strip">
    <span>&#9742;&nbsp; +1 555 014 2270</span><span class="sep"></span>
    <span>&#9993;&nbsp; info@k7momentum.com</span><span class="sep"></span>
    <div class="social"><span></span><span></span><span></span><span></span></div>
  </div>
  <nav class="abs main-nav">
    <a class="current" href="#">Home</a><a href="#">About</a><a href="#">Our Team</a><a href="#">Plan Elements</a><a href="#">FAQ</a><a href="#">The Solutions</a><a href="#">Our Partners</a><a href="#">Contact Us</a>
    <span class="search-btn"><svg width="12" height="12" viewBox="0 0 12 12"><circle cx="5" cy="5" r="3.5" fill="none" stroke="#222" stroke-width="1.6"/><line x1="7.6" y1="7.6" x2="11" y2="11" stroke="#222" stroke-width="1.6"/></svg></span>
  </nav>
</header>

<section class="hero">
  <div class="abs hero-photo" role="img" aria-label="Three colleagues meeting around a laptop in a bright office lounge"></div>
  <h1 class="abs">Welcome To K7 Momentum Collective</h1>
  <span class="abs btn">Get Started</span>
</section>

<section class="about">
  <div class="abs about-accent" role="img" aria-label="Decorative dotted grid accent"></div>
  <div class="abs about-photo" role="img" aria-label="Businessman at a laptop with overlaid growth chart graphics"></div>
  <h2 class="abs">About <span class="accent">K7 Momentum Collective</span></h2>
  <div class="abs copy">
    <p>The K7 Momentum Collective (K7) rapidly brings innovative &amp;<br>transformational IP to market by assisting with all elements of a<br>company's development.</p>
    <ul class="ticks">
      <li><svg width="13" height="12" viewBox="0 0 13 12"><path d="M1 6h10M7 2l4 4-4 4" stroke="#2f8fa3" stroke-width="2.2" fill="none"/></svg>We Are...experienced in strategic business planning and execution,<br>and operational excellence.</li>
      <li><svg width="13" height="12" viewBox="0 0 13 12"><path d="M1 6h10M7 2l4 4-4 4" stroke="#2f8fa3" stroke-width="2.2" fill="none"/></svg>We Have...100 years of collective experiences and vast network of<br>people, partners, and processes.</li>
      <li><svg width="13" height="12" viewBox="0 0 13 12"><path d="M1 6h10M7 2l4 4-4 4" stroke="#2f8fa3" stroke-width="2.2" fill="none"/></svg>We Can...serve as the initial executive team to ensure strategic<br>alignment with a focus on marketplace.</li>
      <li><svg width="13" height="12" viewBox="0 0 13 12"><path d="M1 6h10M7 2l4 4-4 4" stroke="#2f8fa3" stroke-width="2.2" fill="none"/></svg>We Will...remove the uncertainty and confusion common in the initial<br>stages of a company's formation.</li>
    </ul>
  </div>
  <span class="abs btn">Read More</span>
</section>

<section class="discovery">
  <h2 class="abs section-title">Discovery <span class="accent">to Market</span></h2>
  <div class="abs card" style="left:63px">
    <svg width="96" height="92" viewBox="0 0 96 92" fill="none" stroke="#111" stroke-width="3"><circle cx="56" cy="36" r="30"/><circle cx="56" cy="36" r="22"/><path d="M34 58 10 82l6 6 24-24"/><path d="M50 44h12M52 49h8M49 38c-4-4-3-12 7-12s11 8 7 12"/></svg>
    <h3>Discovery</h3><p>Business model, Org structure &amp;<br>planning, Cash planning,Fund<br>raising</p>
  </div>
  <div class="abs card" style="left:337px">
    <svg width="96" height="92" viewBox="0 0 96 92" fill="none" stroke="#111" stroke-width="3"><circle cx="64" cy="28" r="12"/><circle cx="64" cy="28" r="20" stroke-dasharray="6 4"/><circle cx="30" cy="54" r="9"/><circle cx="30" cy="54" r="16" stroke-dasharray="5 4"/><path d="M44 80h14M46 86h10M50 70v-10"/></svg>
    <h3>Innovative IP</h3><p>Inventor Disclosure,Provisional<br>Patent,Licensing<br>agreement</p>
  </div>
  <div class="abs card active" style="left:611px">
    <svg width="96" height="92" viewBox="0 0 96 92" fill="none" stroke="#fff" stroke-width="3"><rect x="10" y="10" width="62" height="46"/><path d="M22 46V34M32 46V26M42 46V32M20 26l12-8 10 6 14-10"/><circle cx="66" cy="52" r="13"/><path d="M75 61l12 12M24 56l-8 24M58 56l8 24"/></svg>
    <h3>Strategic Business Plan</h3><p>Invention Assessment,Voice of<br>Customer,Product Definition<br>Business Model/Plan,Pitch Deck</p>
  </div>
  <div class="abs card" style="left:886px">
    <svg width="96" height="92" viewBox="0 0 96 92" fill="none" stroke="#111" stroke-width="3"><rect x="30" y="6" width="60" height="40"/><path d="M40 18h40M40 28h30"/><circle cx="20" cy="30" r="8"/><path d="M6 56h34v8H6zM12 64v20M34 64v20"/><circle cx="46" cy="70" r="6"/><circle cx="72" cy="70" r="6"/><path d="M36 88c0-8 20-8 20 0M62 88c0-8 20-8 20 0"/></svg>
    <h3>Company Formation</h3><p>Experienced management<br>How to build out the initial team<br>Product definition</p>
  </div>
</section>

<section class="problem">
  <div class="abs problem-photo" role="img" aria-label="Man in glasses working on a laptop by a window"></div>
  <div class="abs problem-shade"></div>
  <h2 class="abs">The Problem &gt; <b>The Solution</b></h2>
  <div class="abs copy">
    <p>K7 was started to solve significant problems associated with rapidly<br>bringing innovative and transformational IP to market. These costly<br>problems include:</p>
    <ul>
      <li><svg width="12" height="11" viewBox="0 0 12 11"><path d="M1 5.5h9M6 1.5l4 4-4 4" stroke="#fff" stroke-width="2" fill="none"/></svg>Incomplete strategic planning, Difficulty finding leadership,</li>
      <li><svg width="12" height="11" viewBox="0 0 12 11"><path d="M1 5.5h9M6 1.5l4 4-4 4" stroke="#fff" stroke-width="2" fill="none"/></svg>Not able to differentiate a product or service from others that are already<br>available, andIgnoring the needs of customer.</li>
    </ul>
    <p>(Capital shortages, poor locations, and scaling too soon can also cause a<br>start-up to have problems.)</p>
  </div>
  <span class="abs btn-light">Learn More</span>
</section>

<section class="team">
  <h2 class="abs section-title">Our <span class="accent">Team</span></h2>
  <div class="abs member" style="left:111px;top:110px">
    <div class="photo" role="img" aria-label="Portrait of team member with arms crossed"></div>
    <div class="name">RL Harmon</div>
    <p>30+ years of marketing, sales,<br>product development, and operations<br>executive leader in the life science</p>
    <div class="mail">&#9993; rl@k7mc.com</div>
  </div>
  <div class="abs member mid" style="left:463px;top:143px">
    <div class="photo" role="img" aria-label="Portrait of smiling team member"></div>
    <div class="name">Nina Castell</div>
    <p>30+ years working in diagnostic and<br>medical device area with focus on<br>creative solutions</p>
    <div class="mail">&#9993; nina@k7mc.com</div>
  </div>
  <div class="abs member" style="left:815px;top:110px">
    <div class="photo" role="img" aria-label="Portrait of team member in grey t-shirt"></div>
    <div class="name">DW Prescott</div>
    <p>30+ years accomplished CEO and<br>well-rounded executive with more<br>than 25 years of experience in</p>
    <div class="mail">&#9993; dw@k7mc.com</div>
  </div>
</section>

<section class="contact">
  <h2 class="abs section-title">Get In <span class="accent">Touch With Us</span></h2>
  <h4 class="abs">Address</h4>
  <div class="abs info" style="top:152px"><span class="ico"><svg width="16" height="20" viewBox="0 0 16 20"><path d="M8 0a8 8 0 0 0-8 8c0 6 8 12 8 12s8-6 8-12a8 8 0 0 0-8-8z" fill="#fff"/><circle cx="8" cy="8" r="3" fill="#4472c6"/></svg></span><span>K7 Momentum Collective<br>United States</span></div>
  <div class="abs info" style="top:223px"><span class="ico"><svg width="18" height="18" viewBox="0 0 18 18"><path d="M4 1 7 5 5 7c1 2 4 5 6 6l2-2 4 3-2 3C9 17 1 9 1 3z" fill="#fff"/></svg></span><span>+1 555 014 2270</span></div>
  <div class="abs info" style="top:286px"><span class="ico"><svg width="18" height="14" viewBox="0 0 18 14"><rect width="18" height="14" rx="2" fill="#fff"/><path d="M1 2l8 6 8-6" stroke="#4472c6" stroke-width="1.6" fill="none"/></svg></span><span>info@k7momentum.com</span></div>
  <div class="abs field" style="left:509px;top:100px;width:283px;height:51px">First Name</div>
  <div class="abs field" style="left:803px;top:100px;width:283px;height:51px">Last Name</div>
  <div class="abs field" style="left:509px;top:163px;width:283px;height:51px">Your Phone</div>
  <div class="abs field" style="left:803px;top:163px;width:283px;height:51px">Your Email</div>
  <div class="abs field" style="left:509px;top:226px;width:577px;height:112px;align-items:flex-start;padding-top:16px">Message</div>
  <span class="abs btn">Submit</span>
</section>

<footer class="site-footer">
  <div class="abs name">K7 Momentum Collective</div>
  <nav class="abs foot-nav"><span>Home</span><span>About</span><span>Our Team</span><span>Plan Elements</span><span>The Solutions</span><span>Our Partners</span><span>Contact Us</span></nav>
  <div class="abs foot-social"><span></span><span></span><span></span><span></span></div>
  <div class="abs copyright">Copyrights@2023.K7 Momentum Collective.All Rights Reserved</div>
</footer>

</body>
</html>
```